Electric mountain bike tours nz

We are an Electric Mountain bike tour company in New Zealand. We will be offering bike rental and guided tours around the Nelson region in New Zealand. I want our website to represent both Mountain biking and New Zealand with the colours layout and features. We want tabs for the following:
-1 about us
-2 what we offer
-3 bookings/contact
Under the about us tab will be who we are as a a company. I want the ability to add videos to each of these tabs as we move foward with videos of the tracks we will be riding. I want the website to be editable so I can add and remove videos/photos myself. Also "our bikes" will be under this tab.
Under the what we offer tab will be
-1 bike rental and pricing
-2 guided tours and pricing
-3 recommended package deals.
I want to able to put the tracks under the guided tours tab and select beginner/ intermediate/advanced and have the tracks in each of the following to match the rider level. Also to be able to have a small video of the track would be great in this section.
Bookings and contact tab
(Further information for this tab to be updated soon)
Coded - Design and coding required
1 page
- Silver ferns, kiwi, mountains

```html
<!DOCTYPE html>
<html lang="en">
<head>
<meta charset="utf-8">
<title>RIDGEVOLT – Electric Mountain Bike Tours</title>
<link rel="stylesheet" href="https://fonts.googleapis.com/css2?family=Lato:wght@400;700;900&display=swap">
<style>
:root{
  --ink:#1b1b1b;
  --muted:#5c5c5c;
  --light:#ffffff;
  --grey-band:#b4b4b4;
  --green:#5aa51b;
  --green-dark:#2f6b0c;
  --dark:#202225;
  --hero-a:#3c3f3a;
  --hero-b:#1e211f;
}
*{margin:0;padding:0;box-sizing:border-box}
html,body{width:1200px;height:3232px;overflow:hidden}
body{position:relative;font-family:'Lato',sans-serif;color:var(--ink);background:var(--light)}
.abs{position:absolute}
.photo{position:absolute}

/* hero */
.hero{position:absolute;left:0;top:0;width:1200px;height:765px;background:linear-gradient(180deg,#5a5e5a 0%,var(--hero-a) 45%,var(--hero-b) 100%)}
.brand{position:absolute;left:82px;top:90px;display:flex;align-items:center;gap:10px;color:#fff;font-weight:900;font-size:24px;letter-spacing:1px}
.brand .dot{width:22px;height:22px;border-radius:50%;background:#fff}
.nav{position:absolute;left:446px;top:73px;width:754px;height:48px;background:#fff;border-radius:24px 0 0 24px;box-shadow:0 2px 6px rgba(0,0,0,.3)}
.nav a{position:absolute;top:15px;font-size:14px;font-weight:700;color:var(--ink);text-decoration:none}
.nav .bolt{position:absolute;top:15px}
.social{display:flex;gap:6px}
.social span{width:18px;height:18px;border-radius:50%;background:var(--ink);display:block}
.hero h1{position:absolute;left:0;width:1200px;top:385px;text-align:center;color:#fff;font-weight:900;font-size:58px;letter-spacing:2px}
.hero p{position:absolute;left:0;width:1200px;top:456px;text-align:center;color:#fff;font-size:14px;line-height:24px}
.book-now{position:absolute;left:517px;top:536px;width:164px;height:41px;border:2px solid #fff;color:#fff;font-size:14px;font-weight:700;display:flex;align-items:center;justify-content:center;padding-left:20px}

/* buttons */
.btn{position:absolute;width:151px;height:40px;background:#111;color:#fff;font-size:14px;font-weight:700;display:flex;align-items:center;padding-left:42px}
.btn.light{background:#fff;color:var(--ink)}
.btn svg{position:absolute;left:-6px;top:-4px}

/* headings */
.sec-title{position:absolute;font-size:27px;font-weight:900;color:var(--ink)}
.sec-title em{font-style:normal;font-weight:400;color:#9a9a9a}
.sec-title.center{left:0;width:1200px;text-align:center}
.peak{position:absolute}
.body-text{position:absolute;font-size:14px;line-height:23px;color:var(--muted)}

/* bikes band */
.bikes{position:absolute;left:0;top:1217px;width:1200px;height:377px;background:linear-gradient(180deg,#4a5046,#2e332e)}
.bikes .sec-title{color:#fff}
.bikes .sec-title em{color:#d8d8d8}
.bikes .body-text{color:#fff}

/* offers */
.offer{position:absolute;top:1745px;width:289px}
.offer h3{font-size:21px;font-weight:700;margin-bottom:20px}
.offer .pic{height:241px}
.offer h4{font-size:16px;font-weight:900;margin-top:22px}
.offer p{font-size:12px;line-height:18px;color:var(--muted);margin-top:6px}

/* newsletter */
.news{position:absolute;left:0;top:2322px;width:1200px;height:73px;background:var(--green)}
.news .label{position:absolute;left:253px;top:22px;color:#fff;font-size:27px}
.news .input{position:absolute;left:532px;top:21px;width:401px;height:32px;background:#fff;font-size:10px;color:#777;padding:10px 14px}
.news .sub{position:absolute;left:943px;top:21px;width:134px;height:32px;background:var(--green-dark);color:#fff;font-size:13px;font-weight:900;display:flex;align-items:center;justify-content:center;letter-spacing:.5px}

/* blog & testimonials */
.lower{position:absolute;left:0;top:2395px;width:1200px;height:384px;background:var(--grey-band)}
.lower h2{position:absolute;font-size:26px;font-weight:700;color:var(--ink)}
.arrows{position:absolute;display:flex;gap:6px}
.arrows span{width:19px;height:19px;border-radius:50%;background:var(--ink);display:flex;align-items:center;justify-content:center}
.post{position:absolute;left:84px;width:480px;display:flex;gap:15px}
.post .thumb{width:84px;height:84px;border:2px solid #fff;flex:none}
.post h5{font-size:16px;font-weight:900;margin-top:2px}
.post p{font-size:12.5px;line-height:18px;color:var(--ink);margin-top:2px}
.post small{font-size:12.5px;display:block;margin-top:2px}
.quote{position:absolute;left:825px;top:2534px;width:297px;font-size:12.5px;line-height:19.5px;color:var(--ink)}

/* footer */
.footer{position:absolute;left:0;top:2779px;width:1200px;height:453px;background:linear-gradient(180deg,#2d302e,#141615)}
.footer-brand{position:absolute;left:159px;top:2895px;width:229px;display:flex;align-items:center;justify-content:center;gap:10px;color:#fff;font-weight:900;font-size:26px}
.footer-brand .dot{width:24px;height:24px;border-radius:50%;background:#fff}
.footer-about{position:absolute;left:159px;top:3012px;width:229px;font-size:12.5px;line-height:19px;color:#fff;text-align:justify}
.booking{position:absolute;left:452px;top:2828px;width:295px;height:308px;background:#fff;padding:20px 50px}
.booking h3{text-align:center;font-size:19px;font-weight:900;margin-bottom:14px}
.field{border-bottom:1px solid #aaa;font-size:10px;color:#888;height:20px;margin-bottom:22px}
.field.area{border:1px solid #aaa;height:62px;padding:4px}
.send{width:80px;height:22px;background:#111;color:#fff;font-size:11px;margin:14px auto 0;display:flex;align-items:center;justify-content:center}
.contact{position:absolute;left:814px;top:2846px;width:200px;color:#fff}
.contact h3{font-size:19px;font-weight:700;padding-bottom:10px;border-bottom:1px solid #666;margin-bottom:22px}
.contact p{font-size:12.5px;line-height:19px;margin-bottom:9px;display:flex;align-items:flex-start;gap:6px}
.follow{position:absolute;left:814px;top:3043px;color:#fff;font-size:17px;font-weight:900;letter-spacing:.5px;padding-bottom:10px;border-bottom:1px solid #666;width:200px}
.footer .social span{background:#fff}
.copy{position:absolute;left:0;top:3180px;width:1200px;text-align:center;color:#bbb;font-size:13px}
</style>
</head>
<body>

<!-- HERO -->
<section class="hero">
  <div class="photo" style="inset:0;background:radial-gradient(ellipse at 30% 60%,rgba(120,110,90,.35),transparent 60%)" role="img" aria-label="Rider on an electric mountain bike in a rocky New Zealand valley"></div>
  <div class="brand"><span class="dot"></span>RIDGEVOLT</div>
  <nav class="nav">
    <a style="left:104px">About us</a>
    <svg class="bolt" style="left:220px" width="10" height="16" viewBox="0 0 10 16"><path d="M6 0 0 9h4l-2 7 8-10H6l2-6z" fill="#aaa"/></svg>
    <a style="left:265px">What we offer</a>
    <svg class="bolt" style="left:380px" width="10" height="16" viewBox="0 0 10 16"><path d="M6 0 0 9h4l-2 7 8-10H6l2-6z" fill="#aaa"/></svg>
    <a style="left:424px">Bookings/Contact</a>
    <div class="social abs" style="left:560px;top:15px"><span></span><span></span><span></span><span></span><span></span></div>
  </nav>
  <h1>RIDGEVOLT</h1>
  <p>We are an Electric Mountain bike tour company in New Zealand. We will be offering bike rental<br>and guided tours around the Nelson region in New Zealand.</p>
  <div class="book-now">
    <svg class="abs" style="left:-6px;top:-8px" width="26" height="42" viewBox="0 0 26 42"><path d="M17 0 2 24h9L6 42 24 15h-9l6-15z" fill="#fff"/></svg>
    BOOK NOW
  </div>
</section>

<!-- ABOUT -->
<svg class="peak" style="left:132px;top:810px" width="34" height="16" viewBox="0 0 34 16"><path d="M0 16 12 3l5 5 5-8 12 16h-4l-8-10-5 7-5-5-8 8z" fill="#111"/></svg>
<h2 class="sec-title" style="left:90px;top:826px">About <em>Us</em></h2>
<div class="abs" style="left:90px;top:868px;width:124px;height:2px;background:#111"></div>
<p class="body-text" style="left:90px;top:897px;width:556px">Lorem ipsum dolor sit amet, consectetuer adipiscing elit. Aenean commodo ligula eget dolor. Aenean massa. Cum sociis natoque penatibus et magnis dis parturient montes, nascetur ridiculus mus. Donec quam felis, ultricies nec, pellentesque eu, pretium quis, sem. Nulla consequat massa quis enim. Donec pede justo, fringilla vel, aliquet nec, vulputate eget, arcu. In enim justo, rhoncus ut, imperdiet a, venenatis vitae, justo. Nullam dictum felis eu pede mollis pretium. Integer tincidunt. Cras dapibus. Vivamus elementum semper nisi.</p>
<div class="btn" style="left:90px;top:1103px">
  <svg width="30" height="48" viewBox="0 0 30 48"><path d="M20 0 2 28h11L7 48 28 17H17l7-17z" fill="#fff" stroke="#111" stroke-width="2"/></svg>
  Read More
</div>
<div class="photo" style="left:717px;top:905px;width:397px;height:237px;background:linear-gradient(180deg,#6d8fb5,#c9d7e4 55%,#3e4a55)" role="img" aria-label="Video of a rider's view on a snowy mountain bike trail"></div>
<svg class="abs" style="left:895px;top:1000px" width="40" height="40" viewBox="0 0 40 40"><circle cx="20" cy="20" r="19" fill="#fff" opacity=".9"/><path d="M16 12v16l12-8z" fill="#111"/></svg>
<div class="abs" style="left:717px;top:1110px;width:397px;height:32px;background:rgba(0,0,0,.55)"></div>
<svg class="abs" style="left:730px;top:1118px" width="30" height="16" viewBox="0 0 30 16"><path d="M0 2v12l9-6z" fill="#fff"/><rect x="16" y="2" width="4" height="12" fill="#fff"/><rect x="23" y="2" width="4" height="12" fill="#fff"/></svg>
<div class="abs" style="left:776px;top:1124px;width:320px;height:4px;background:#ddd"></div>
<div class="abs" style="left:776px;top:1124px;width:120px;height:4px;background:#d11"></div>

<!-- OUR BIKES -->
<section class="bikes">
  <div class="photo" style="inset:0;background:radial-gradient(ellipse at 70% 80%,rgba(110,110,100,.4),transparent 60%)" role="img" aria-label="Winding mountain road background"></div>
  <svg class="peak" style="left:583px;top:23px" width="34" height="16" viewBox="0 0 34 16"><path d="M0 16 12 3l5 5 5-8 12 16h-4l-8-10-5 7-5-5-8 8z" fill="#fff"/></svg>
  <h2 class="sec-title center" style="top:40px">Our <em>Bikes</em></h2>
  <div class="photo" style="left:144px;top:125px;width:427px;height:198px;background:linear-gradient(180deg,#9aa39a,#b9bdb6 60%,#8a8f88)" role="img" aria-label="Electric mountain bike parked on a road"></div>
  <p class="body-text" style="left:610px;top:120px;width:504px;font-size:14px;line-height:24px">Lorem ipsum dolor sit amet, consectetuer adipiscing elit. Aenean commodo ligula eget dolor. Aenean massa. Cum sociis natoque penatibus et magnis dis parturient montes, nascetur ridiculus mus. Donec quam felis, ultricies nec, pellentesque eu, pretium quis, sem. Nulla consequat massa quis enim. Donec pede justo, fringilla vel, aliquet nec, vulputate eget, arcu.</p>
  <div class="btn light" style="left:614px;top:284px">
    <svg width="30" height="48" viewBox="0 0 30 48"><path d="M20 0 2 28h11L7 48 28 17H17l7-17z" fill="#111" stroke="#fff" stroke-width="2"/></svg>
    Read More
  </div>
</section>

<!-- WHAT WE OFFER -->
<svg class="peak" style="left:583px;top:1645px" width="34" height="16" viewBox="0 0 34 16"><path d="M0 16 12 3l5 5 5-8 12 16h-4l-8-10-5 7-5-5-8 8z" fill="#111"/></svg>
<h2 class="sec-title center" style="top:1663px">What we <em>Offer</em></h2>

<article class="offer" style="left:144px">
  <h3>Bike rental &amp; pricing</h3>
  <div class="pic" style="background:linear-gradient(180deg,#7fa6cc,#c9d6d8 40%,#3d5a6e 70%,#2d3b30)" role="img" aria-label="Mountain bike overlooking a valley at sunrise"></div>
  <h4>Lorem ipsum dolor</h4>
  <p>Lorem ipsum dolor sit amet, consectetuer adipiscing elit. Aenean commodo ligula eget dolor. Aenean massa. Cum sociis natoque penatibus et magnis dis parturient montes, nascetur ridiculus mus. Donec quam felis, ultricies nec, pellentesque eu, pretium quis, sem. Nulla consequat massa quis enim.</p>
</article>
<article class="offer" style="left:459px">
  <h3>Guided tours &amp; pricing</h3>
  <div class="pic" style="background:linear-gradient(180deg,#b7c7d4,#a8a49a 50%,#5e5a52)" role="img" aria-label="Two riders with electric mountain bikes"></div>
  <h4>Beginner</h4>
  <p>Lorem ipsum dolor sit amet, consectetuer adipiscing elit. Aenean commodo ligula eget dolor. Aenean massa. Cum sociis natoque penatibus et magnis dis parturient montes, nascetur ridiculus mus. Donec quam felis, ultricies nec, pellentesque eu, pretium quis, sem. Nulla consequat massa quis enim.</p>
</article>
<article class="offer" style="left:771px">
  <h3>Recommended package deals</h3>
  <div class="pic" style="background:linear-gradient(180deg,#8fb36a,#5e8a3c 50%,#8c7a5a)" role="img" aria-label="Riders on a forest trail"></div>
  <h4>Lorem ipsum dolor</h4>
  <p>Lorem ipsum dolor sit amet, consectetuer adipiscing elit. Aenean commodo ligula eget dolor. Aenean massa. Cum sociis natoque penatibus et magnis dis parturient montes, nascetur ridiculus mus. Donec quam felis, ultricies nec, pellentesque eu, pretium quis, sem. Nulla consequat massa quis enim.</p>
</article>
<div class="btn" style="left:144px;top:2210px"><svg width="30" height="48" viewBox="0 0 30 48"><path d="M20 0 2 28h11L7 48 28 17H17l7-17z" fill="#fff" stroke="#111" stroke-width="2"/></svg>Read More</div>
<div class="btn" style="left:459px;top:2210px"><svg width="30" height="48" viewBox="0 0 30 48"><path d="M20 0 2 28h11L7 48 28 17H17l7-17z" fill="#fff" stroke="#111" stroke-width="2"/></svg>Read More</div>
<div class="btn" style="left:771px;top:2210px"><svg width="30" height="48" viewBox="0 0 30 48"><path d="M20 0 2 28h11L7 48 28 17H17l7-17z" fill="#fff" stroke="#111" stroke-width="2"/></svg>Read More</div>

<!-- NEWSLETTER -->
<section class="news">
  <svg class="abs" style="left:200px;top:18px" width="38" height="38" viewBox="0 0 38 38"><circle cx="19" cy="19" r="18" fill="#fff"/><rect x="10" y="13" width="18" height="12" fill="var(--green)"/><path d="M10 13l9 7 9-7" fill="none" stroke="#fff" stroke-width="1.5"/></svg>
  <div class="label">News letter Signup</div>
  <svg class="abs" style="left:490px;top:14px" width="20" height="46" viewBox="0 0 20 46"><path d="M2 2l16 21L2 44" fill="none" stroke="#fff" stroke-width="2"/></svg>
  <div class="input">Enter Your Email</div>
  <div class="sub">SUBSCRIBE</div>
</section>

<!-- BLOG & TESTIMONIALS -->
<section class="lower">
  <h2 style="left:84px;top:43px">Latest Blog</h2>
  <div class="arrows" style="left:510px;top:50px">
    <span><svg width="8" height="10" viewBox="0 0 8 10"><path d="M6 1 2 5l4 4" fill="none" stroke="#fff" stroke-width="2"/></svg></span>
    <span><svg width="8" height="10" viewBox="0 0 8 10"><path d="M2 1l4 4-4 4" fill="none" stroke="#fff" stroke-width="2"/></svg></span>
  </div>
  <div class="abs" style="left:84px;top:90px;width:480px;height:1px;background:#888"></div>
  <div class="abs" style="left:603px;top:45px;width:1px;height:310px;background:#888"></div>
  <h2 style="left:657px;top:43px">Testimonials</h2>
  <div class="arrows" style="left:1077px;top:50px">
    <span><svg width="8" height="10" viewBox="0 0 8 10"><path d="M6 1 2 5l4 4" fill="none" stroke="#fff" stroke-width="2"/></svg></span>
    <span><svg width="8" height="10" viewBox="0 0 8 10"><path d="M2 1l4 4-4 4" fill="none" stroke="#fff" stroke-width="2"/></svg></span>
  </div>
  <div class="abs" style="left:657px;top:90px;width:463px;height:1px;background:#888"></div>
</section>

<div class="post" style="top:2527px">
  <div class="thumb" style="background:linear-gradient(180deg,#6f8a4a,#4a5a32)" role="img" aria-label="Rider on a forest trail"></div>
  <div><h5>Verum tamen cum de rebus</h5><p>Lorem ipsum dolor sit amet, consectetuer adipiscing elit. Quid utem habent admirationis,</p><small>10-Oct 2017</small></div>
</div>
<div class="post" style="top:2643px">
  <div class="thumb" style="background:linear-gradient(180deg,#9aa0a6,#6a6258)" role="img" aria-label="Riders resting with their bikes"></div>
  <div><h5>Verum tamen cum de rebus</h5><p>Lorem ipsum dolor sit amet, consectetuer adipiscing elit. Quid utem habent admirationis,</p><small>10-Oct 2017</small></div>
</div>

<div class="photo" style="left:657px;top:2531px;width:146px;height:150px;background:linear-gradient(180deg,#8a8e92,#5a5e62)" role="img" aria-label="Portrait of a customer"></div>
<div class="abs" style="left:657px;top:2681px;width:146px;height:33px;background:#111;color:#fff;font-size:12px;font-weight:900;display:flex;align-items:center;justify-content:center">MR HALE</div>
<p class="quote"><b style="font-size:20px;line-height:10px">&ldquo;</b> Lorem ipsum dolor sit amet, consectetuer adipiscing elit. Aenean commodo ligula eget dolor. Aenean massa. Cum sociis natoque penatibus et magnis dis parturient montes, nascetur ridiculus mus. Donec quam felis, ultricies nec, pellentesque eu, pretium quis, sem. Nulla consequat massa quis enim. Donec pede justo, fringilla vel, aliquet nec, vulputate eget, arcu. In enim justo, rhoncus ut, imperdiet a, venenatis vitae, justo. Nullam dictum felis eu pede mollis pretium. Integer tincidunt. <b style="font-size:20px;line-height:10px">&rdquo;</b></p>

<!-- FOOTER -->
<footer class="footer" role="img" aria-label="Dark mountain landscape background"></footer>
<div class="footer-brand"><span class="dot"></span>RIDGEVOLT</div>
<p class="footer-about">Lorem ipsum dolor sit amet, consectetuer adipiscing elit. Aenean commodo ligula eget dolor. Aenean massa. Cum sociis natoque penatibus et magnis dis parturient montes, nascetur ridiculus mus. Donec quam felis, ultricies nec, pellentesque eu.</p>

<div class="booking">
  <h3>Booking</h3>
  <div class="field">Name</div>
  <div class="field">E-mail</div>
  <div class="field">Phone</div>
  <div class="field area">Message</div>
  <div class="send">Send</div>
</div>

<div class="contact">
  <h3>Contact</h3>
  <p>42 Harbour Row<br>Tasman Bay 7011</p>
  <p><svg width="12" height="12" viewBox="0 0 12 12"><path d="M2 1h3l1 3-2 1a7 7 0 0 0 3 3l1-2 3 1v3c-6 1-10-3-9-9z" fill="#fff"/></svg>555-204-7731</p>
  <p><svg width="12" height="12" viewBox="0 0 12 12"><rect x="0" y="2" width="12" height="8" fill="#fff"/><path d="M0 2l6 5 6-5" fill="none" stroke="#222"/></svg>hello@ridgevolt.example</p>
  <p><svg width="12" height="12" viewBox="0 0 12 12"><circle cx="6" cy="6" r="5.5" fill="none" stroke="#fff"/><path d="M0.5 6h11M6 0.5v11" stroke="#fff"/></svg>www.ridgevolt.example</p>
</div>
<div class="follow">FOLLOW US ON</div>
<div class="social abs" style="left:814px;top:3100px;gap:6px"><span style="background:#fff"></span><span style="background:#fff"></span><span style="background:#fff"></span><span style="background:#fff"></span><span style="background:#fff"></span></div>

<div class="copy">© 2017 ridgevolt &nbsp;| &nbsp;Privacy Policy &nbsp;| &nbsp;User Agreement</div>

</body>
</html>
```